Wine label for family vineyard start-up

Brand new family vineyard needs a new label:

The information we need on the label is the following:
- Merlot & Cabernet (variety)
- Ponte Capriasca (location)
- 2016 (vintage)

The style of the label should be graphic / minimal / masculine.

This is a wine made by three 35yr old guys

Target Market(s)

young & urban

Industry/Entity Type

Vineyard

Logo Text

Merlot & Cabernet / Ponte Capriasca / 2016

Font styles to use
Sans Serif

Requirements
Must have
• clearly legible
• aesthetically pleasing [minimalist]
• sans serif

```html
<!DOCTYPE html>
<html lang="en">
<head>
<meta charset="utf-8">
<title>Ponte Capriasca 2016 – Label Variants</title>
<link rel="stylesheet" href="https://fonts.googleapis.com/css2?family=Arimo:wght@700&family=Delius&family=Questrial&family=Sacramento&display=swap">
<style>
  :root {
    --paper: #ffffff;
    --ink: #000000;
    --label-bg: #000000;
    --label-text: #ffffff;
    --frame-line: #1a1a1a;
  }
  * { box-sizing: border-box; margin: 0; padding: 0; }
  html, body {
    width: 846px;
    height: 1200px;
    overflow: hidden;
    background: var(--paper);
  }
  .sheet {
    position: relative;
    width: 846px;
    height: 1200px;
    background: var(--paper);
    border: 2px solid var(--frame-line);
  }
  .label-frame {
    position: absolute;
    width: 408px;
    height: 587px;
    border: 2px solid var(--frame-line);
    background: var(--paper);
  }
  .label-frame.top { top: 9px; }
  .label-frame.bottom { top: 603px; }
  .label-frame.left { left: 9px; }
  .label-frame.right { left: 428px; }

  .label {
    position: absolute;
    inset: 8px;
    background: var(--label-bg);
    color: var(--label-text);
  }
  .brand-mark {
    position: absolute;
    top: 140px;
    left: 0;
    right: 0;
    height: 200px;
    display: flex;
    align-items: center;
    justify-content: center;
    gap: 14px;
    color: var(--label-text);
  }
  .brand-mark .brand-square {
    width: 22px;
    height: 22px;
    background: var(--label-text);
  }
  .brand-mark .brand-name {
    font-size: 44px;
    letter-spacing: 2px;
    line-height: 1;
  }
  .line {
    position: absolute;
    left: 0;
    right: 0;
    text-align: center;
    line-height: 1;
    white-space: nowrap;
  }

  /* Variant 1 – rounded casual sans */
  .variant-rounded { font-family: "Delius", sans-serif; }
  .variant-rounded .brand-name { font-size: 40px; }
  .variant-rounded .vintage { top: 392px; font-size: 27px; }
  .variant-rounded .place { top: 448px; font-size: 27px; }
  .variant-rounded .variety { top: 490px; font-size: 27px; }

  /* Variant 2 – monoline script */
  .variant-script { font-family: "Sacramento", cursive; }
  .variant-script .brand-name { font-size: 54px; letter-spacing: 0; }
  .variant-script .vintage { top: 393px; font-size: 24px; }
  .variant-script .place { top: 442px; font-size: 34px; }
  .variant-script .variety { top: 490px; font-size: 34px; }

  /* Variant 3 – light geometric sans */
  .variant-geometric { font-family: "Questrial", sans-serif; }
  .variant-geometric .vintage { top: 389px; font-size: 33px; }
  .variant-geometric .place { top: 446px; font-size: 32px; }
  .variant-geometric .variety { top: 491px; font-size: 32px; }

  /* Variant 4 – bold grotesk caps */
  .variant-grotesk { font-family: "Arimo", sans-serif; font-weight: 700; }
  .variant-grotesk .brand-name { font-size: 40px; }
  .variant-grotesk .vintage { top: 393px; font-size: 31px; }
  .variant-grotesk .variety { top: 446px; font-size: 23px; }
  .variant-grotesk .place { top: 497px; font-size: 23px; }
</style>
</head>
<body>
<main class="sheet">

  <section class="label-frame top left">
    <div class="label variant-rounded">
      <div class="brand-mark"><span class="brand-square"></span><span class="brand-name">TRE COLLI</span></div>
      <p class="line vintage">2016</p>
      <p class="line place">Ponte Capriasca</p>
      <p class="line variety">Merlot &amp; Cabernet</p>
    </div>
  </section>

  <section class="label-frame top right">
    <div class="label variant-script">
      <div class="brand-mark"><span class="brand-square"></span><span class="brand-name">Tre Colli</span></div>
      <p class="line vintage">2016</p>
      <p class="line place">Ponte Capriasca</p>
      <p class="line variety">Merlot &amp; Cabernet</p>
    </div>
  </section>

  <section class="label-frame bottom left">
    <div class="label variant-geometric">
      <div class="brand-mark"><span class="brand-square"></span><span class="brand-name">TRE COLLI</span></div>
      <p class="line vintage">2016</p>
      <p class="line place">Ponte Capriasca</p>
      <p class="line variety">Merlot &amp; Cabernet</p>
    </div>
  </section>

  <section class="label-frame bottom right">
    <div class="label variant-grotesk">
      <div class="brand-mark"><span class="brand-square"></span><span class="brand-name">TRE COLLI</span></div>
      <p class="line vintage">2016</p>
      <p class="line variety">MERLOT / CABERNET</p>
      <p class="line place">PONTE CAPRIASCA</p>
    </div>
  </section>

</main>
</body>
</html>
```